Volunteer fire fighters needed banner

As part of our recruitment campaign, we need a sign we can post on our sign trailer to entice locals to join our volunteer fire service. This design will be printed on a banner, front and back, to catch traffic going in both directions on a busy roadway. This banner will have a printed surface of 4 feet tall by 8 feet long.
Our fire department is looking to attract people between the ages of 18 and 35 years old who are interested in being a firefighter. We offer our volunteers:
-Free professional training
-All equipment supplied
-Tax abatements for active volunteers
For more information, you can check us out at:
Brackenmoorfire.example

This design should:
-scale to and fit a 4'x8' canvas
-Include our web address "BrackenMoorFire.example"
-Say "Members Wanted"
-"Drill every Tuesday at 7pm"
-"57 Kestrel Pond Lane"
-Include "Bracken Moor Fire Department"

We've included reference photos and past images we use for our other campaigns for inspiration for you.

Target Market(s)

18-35 y/o

Industry/Entity Type

Fire Service

Requirements
Must have
• -scale to and fit a 4'x8' canvas -Include our web address "BrackenMoorFire.example" -Say "Members Wanted" -"Drill every Tuesday at 7pm" -"57 Kestrel Pond Lane" -Include "Bracken Moor Fire Department"

```html
<!DOCTYPE html>
<html lang="en">
<head>
<meta charset="utf-8">
<title>Bracken Moor Fire Department – Recruitment Banner</title>
<link href="https://fonts.googleapis.com/css2?family=Montserrat:wght@700;800;900&display=swap" rel="stylesheet">
<style>
  :root {
    --page: #f4f4f2;
    --navy: #343a5e;
    --navy-deep: #2a2f4e;
    --white: #ffffff;
    --red: #e3202a;
    --gold: #f2ad1c;
    --photo-night: #3d5a8f;
    --photo-bay: #8c6f64;
    --photo-drill: #a89a80;
  }
  * { box-sizing: border-box; margin: 0; padding: 0; }
  html, body { width: 1200px; height: 1200px; overflow: hidden; }
  body {
    background: var(--page);
    font-family: "Montserrat", sans-serif;
    display: flex; align-items: center; justify-content: center;
  }
  .banner {
    position: relative;
    width: 1120px; height: 560px;
    background: radial-gradient(ellipse at 50% 35%, #3b4268 0%, var(--navy) 45%, var(--navy-deep) 100%);
    overflow: hidden;
  }
  .brand {
    position: absolute; display: flex; align-items: center; gap: 10px;
    color: var(--white); font-weight: 800; text-transform: uppercase; letter-spacing: .4px;
  }
  .brand--left { top: 22px; left: 26px; }
  .brand--right { top: 192px; right: 28px; }
  .brand__mark { flex: none; border-radius: 50%; background: var(--red); }
  .brand--left .brand__mark { width: 44px; height: 44px; }
  .brand--right .brand__mark { width: 30px; height: 30px; }
  .brand__text { display: flex; flex-direction: column; line-height: 1.2; }
  .brand--left .brand__name { font-size: 14px; }
  .brand__tagline { font-size: 12px; color: var(--gold); margin-top: 3px; }
  .brand--right .brand__name { font-size: 10px; line-height: 1.25; }
  .headline {
    position: absolute; top: 104px; left: 0; right: 0; text-align: center;
    color: var(--white); font-weight: 900; font-size: 66px; letter-spacing: 1px; line-height: 1;
    text-transform: uppercase;
  }
  .drill-band {
    position: absolute; top: 188px; left: 50%; transform: translateX(-50%);
    background: var(--red); color: var(--white);
    font-weight: 900; font-size: 34px; text-transform: uppercase;
    padding: 6px 22px; white-space: nowrap; z-index: 2; line-height: 1.1;
  }
  .gallery {
    position: absolute; top: 246px; left: 28px; right: 28px;
    display: flex; justify-content: space-between;
  }
  .photo {
    width: 340px; height: 226px; border: 3px solid var(--gold); border-radius: 3px;
  }
  .photo--hose-lay { background: linear-gradient(160deg, var(--photo-night), #1f2a3a 70%, #3a5a2a); }
  .photo--engine { background: linear-gradient(160deg, #d9d6cf, var(--photo-bay) 50%, #b22a25); }
  .photo--drill { background: linear-gradient(160deg, #e6e3dc, var(--photo-drill) 55%, #6b5a3e); }
  .contact {
    position: absolute; bottom: 24px; display: flex; align-items: center; gap: 8px;
    color: var(--white); font-weight: 800; text-transform: uppercase;
  }
  .contact--web { left: 28px; font-size: 24px; }
  .contact--address { right: 28px; font-size: 20px; }
</style>
</head>
<body>
  <section class="banner">
    <div class="brand brand--left">
      <span class="brand__mark"></span>
      <span class="brand__text">
        <span class="brand__name">Bracken Moor Fire Department</span>
        <span class="brand__tagline">Members Wanted</span>
      </span>
    </div>
    <div class="brand brand--right">
      <span class="brand__mark"></span>
      <span class="brand__text brand__name">Bracken Moor<br>Fire Department</span>
    </div>

    <h1 class="headline">Local Heroes Wanted</h1>
    <p class="drill-band">Drill every Tuesday at 7pm</p>

    <div class="gallery">
      <div class="photo photo--hose-lay" role="img" aria-label="Firefighter laying hose behind an engine at dusk"></div>
      <div class="photo photo--engine" role="img" aria-label="Red fire engine parked in the station bay"></div>
      <div class="photo photo--drill" role="img" aria-label="Firefighter in turnout gear during a training drill"></div>
    </div>

    <div class="contact contact--web">
      <svg width="30" height="30" viewBox="0 0 30 30" aria-hidden="true">
        <circle cx="15" cy="15" r="15" fill="#e3202a"/>
        <g fill="none" stroke="#fff" stroke-width="1.6">
          <circle cx="15" cy="15" r="8"/>
          <ellipse cx="15" cy="15" rx="3.5" ry="8"/>
          <line x1="7" y1="15" x2="23" y2="15"/>
        </g>
      </svg>
      BrackenMoorFire.example
    </div>

    <div class="contact contact--address">
      <svg width="16" height="22" viewBox="0 0 16 22" aria-hidden="true">
        <path d="M8 0C3.6 0 0 3.5 0 7.9 0 13.5 8 22 8 22s8-8.5 8-14.1C16 3.5 12.4 0 8 0z" fill="#e3202a"/>
        <circle cx="8" cy="8" r="3" fill="#343a5e"/>
      </svg>
      57 Kestrel Pond Lane
    </div>
  </section>
</body>
</html>
```